KRWB new business card design

We need a business card design for our established business which is Australia wide however based in Melbourne. We are a young team of Financial Planners who specialize in Insurance and Basic super advice for people like us.

We are people who help our clients get things done in a timely and cost effective manner whilst having a good time and a laugh along the way.

We would like this to have a consistent feel with our new e-brochure which i have attached from a color and font perspective.

Industry/Entity Type

Business

Requirements
Must have
• We do not need specific address details rather just the states we are in:

VIC/NSW/QLD/TAS
Nice to have
• Curved edge to mate the brochure

```html
<!DOCTYPE html>
<html lang="en">
<head>
<meta charset="utf-8">
<title>KRWB business card concepts</title>
<link rel="stylesheet" href="https://fonts.googleapis.com/css2?family=Questrial&family=Mulish:wght@700;800&display=swap">
<style>
:root{
  --ink:#0b0b0b;
  --green:#2f9e49;
  --lime:#8cc63f;
  --white:#ffffff;
  --soft:#d9d9d9;
  --ground:#ecebe8;
  --body:"Questrial", "Century Gothic", sans-serif;
  --head:"Mulish", "Century Gothic", sans-serif;
}
*{box-sizing:border-box;margin:0;padding:0}
html,body{width:1200px;height:502px;overflow:hidden;background:var(--ground)}
.sheet{position:relative;width:1200px;height:502px}
.card{position:absolute;background:var(--ink);color:var(--white);font-family:var(--body);overflow:hidden;border-radius:0 0 22px 0}
.card--rounded-both{border-radius:22px 0 22px 0}

.brand{display:flex;align-items:center;gap:8px;font-family:var(--body);font-size:34px;letter-spacing:1px;color:var(--lime);line-height:1}
.brand__square{width:22px;height:22px;background:var(--green)}
.brand--white{color:var(--white)}
.brand--white .brand__square{background:var(--white)}

.heading{font-family:var(--head);font-weight:800;letter-spacing:2.4px;font-size:13px}
.list{list-style:none}
.list li::before{content:"•";color:var(--lime);margin-right:5px}
.list--white li::before{color:var(--white)}

/* card 1 - contact face */
.c1{left:33px;top:28px;width:354px;height:202px}
.c1 .brand{position:absolute;left:26px;top:84px;flex-direction:column;align-items:flex-start;gap:8px}
.c1 .name-tag{position:absolute;left:146px;top:20px;width:226px;height:36px;background:linear-gradient(180deg,#a6d65a,var(--lime) 60%,#6ea12d);border-radius:5px 0 0 5px;padding:3px 10px;color:#1b3a0a}
.name-tag__name{font-size:12.5px;font-weight:700;font-family:var(--head);color:var(--white)}
.name-tag__name em{font-weight:700}
.name-tag__role{font-size:11px;color:#163309}
.c1 .entity{position:absolute;left:160px;top:68px;font-size:8.6px;line-height:10.5px}
.c1 .contacts{position:absolute;left:160px;top:124px;font-size:8.6px;line-height:14px}
.contacts svg{width:8px;height:8px;vertical-align:-1px;margin-right:3px;fill:var(--white)}
.c1 .states{position:absolute;left:160px;top:176px;font-size:8.6px;letter-spacing:.6px}

/* card 2 */
.c2{left:425px;top:28px;width:354px;height:202px}
.c2 .brand{position:absolute;left:98px;top:44px}
.c2 .heading{position:absolute;left:82px;top:124px}
.c2 .list{position:absolute;left:36px;top:143px;width:270px;font-size:12.3px;line-height:18px;text-align:center}
.c2 .list li{display:inline}
.c2 .photo{position:absolute;right:0;top:0;width:54px;height:202px;background:linear-gradient(180deg,#8a8a8a,#3c3c3c);border-left:3px solid var(--lime);border-bottom-right-radius:22px}

/* card 3 */
.c3{left:815px;top:31px;width:356px;height:205px}
.c3 .brand{position:absolute;left:128px;top:54px}
.c3 .heading{position:absolute;left:111px;top:140px}
.c3 .cols{position:absolute;left:16px;top:165px;display:flex;font-size:11px;line-height:14px}
.c3 .cols .list{padding:0 6px;border-left:1px solid var(--green)}
.c3 .cols .list:first-child{border-left:none}
.c3 .cols .list:last-child{padding-top:14px}

/* card 4 */
.c4{left:36px;top:273px;width:355px;height:207px}
.c4 .brand{position:absolute;left:124px;top:52px}
.c4 .heading{position:absolute;left:113px;top:134px}
.c4 .list{position:absolute;left:20px;top:150px;width:316px;font-size:12.3px;line-height:18px;text-align:center}
.c4 .list li{display:inline}
.c4 .web{position:absolute;left:0;width:100%;top:188px;text-align:center;font-size:12px;letter-spacing:3.6px}

/* card 5 */
.c5{left:432px;top:273px;width:355px;height:202px;border-right:4px solid var(--lime)}
.c5 .brand{position:absolute;left:44px;top:86px}
.c5 .divider{position:absolute;left:174px;top:44px;width:1px;height:118px;background:linear-gradient(180deg,transparent,var(--soft),transparent)}
.c5 .heading{position:absolute;left:192px;top:44px}
.c5 .list{position:absolute;left:192px;top:70px;font-size:12.4px;line-height:21px}

/* card 6 */
.c6{left:818px;top:277px;width:355px;height:207px}
.c6 .heading{position:absolute;left:26px;top:34px;font-size:15px;letter-spacing:3px}
.c6 .list{position:absolute;left:26px;top:58px;font-size:15.4px;line-height:25.4px}
.c6 .brand{position:absolute;left:220px;top:86px}
</style>
</head>
<body>
<main class="sheet">

  <section class="card c1" aria-label="Contact side">
    <div class="brand"><span class="brand__square"></span>KRWB</div>
    <div class="name-tag">
      <div class="name-tag__name">Daniel Marsh <em>ADFS, BBus</em></div>
      <div class="name-tag__role">Financial Adviser</div>
    </div>
    <div class="entity">
      KRWB Pty Ltd<br>
      Authorised Representatives<br>
      Summit Advisory Group Limited<br>
      Australian Financial Services Licensee
    </div>
    <div class="contacts">
      <div><svg viewBox="0 0 10 10"><path d="M2 0h2l1 3-1.5 1a6 6 0 0 0 2.5 2.5L7 5l3 1v2a2 2 0 0 1-2 2A8 8 0 0 1 0 2a2 2 0 0 1 2-2z"/></svg>1300 555 014 &nbsp;<svg viewBox="0 0 10 10"><rect x="2.5" y="0" width="5" height="10" rx="1"/></svg>0400 555 218</div>
      <div><svg viewBox="0 0 10 10"><path d="M2 0h2l1 3-1.5 1a6 6 0 0 0 2.5 2.5L7 5l3 1v2a2 2 0 0 1-2 2A8 8 0 0 1 0 2a2 2 0 0 1 2-2z"/></svg>03 9555 0142 &nbsp;<svg viewBox="0 0 10 10"><path d="M0 2h10v6H0z M0 2l5 4 5-4" stroke="#0b0b0b" stroke-width=".8"/></svg>daniel@krwb.com.au</div>
      <div><svg viewBox="0 0 10 10"><circle cx="5" cy="5" r="5"/></svg>www.krwb.com.au</div>
    </div>
    <div class="states">VIC/NSW/QLD/TAS</div>
  </section>

  <section class="card c2" aria-label="Services side with portrait">
    <div class="brand"><span class="brand__square"></span>KRWB</div>
    <div class="heading">Specialising in:</div>
    <ul class="list">
      <li>Risk Insurance</li> <li>Debt Management</li><br>
      <li>Superannuation</li><br>
      <li>Wealth Creation</li> <li>Retirement Planning</li>
    </ul>
    <div class="photo" role="img" aria-label="Black and white portrait of a smiling team member"></div>
  </section>

  <section class="card c3" aria-label="Services side in columns">
    <div class="brand"><span class="brand__square"></span>KRWB</div>
    <div class="heading">Specialising in:</div>
    <div class="cols">
      <ul class="list"><li>Risk Insurance</li><li>Debt Management</li></ul>
      <ul class="list"><li>Superannuation</li><li>Wealth Creation</li></ul>
      <ul class="list"><li>Retirement Planning</li></ul>
    </div>
  </section>

  <section class="card c4 card--rounded-both" aria-label="Services side in white">
    <div class="brand brand--white"><span class="brand__square"></span>KRWB</div>
    <div class="heading">Specialising in:</div>
    <ul class="list list--white">
      <li>Risk Insurance</li> <li>Debt Management</li> <li>Superannuation</li><br>
      <li>Wealth Creation</li> <li>Retirement Planning</li>
    </ul>
    <div class="web">www.krwb.com.au</div>
  </section>

  <section class="card c5" aria-label="Services side with divider">
    <div class="brand"><span class="brand__square"></span>KRWB</div>
    <div class="divider"></div>
    <div class="heading">Specialising in:</div>
    <ul class="list">
      <li>Risk Insurance</li>
      <li>Debt Management</li>
      <li>Superannuation</li>
      <li>Wealth Creation</li>
      <li>Retirement Planning</li>
    </ul>
  </section>

  <section class="card c6" aria-label="Services side large list">
    <div class="heading">Specialising in:</div>
    <ul class="list">
      <li>Risk Insurance</li>
      <li>Debt Management</li>
      <li>Superannuation</li>
      <li>Wealth Creation</li>
      <li>Retirement Planning</li>
    </ul>
    <div class="brand"><span class="brand__square"></span>KRWB</div>
  </section>

</main>
</body>
</html>
```